Whitcombe Business Card Design

The name of the business is Dario Whitcombe, CPA LLC
The service that we offer is Accounting, Tax & Consulting Services. I need it to have the following items:
Dario Whitcombe, Principal
Phone Number
Email Address
Physical Address

I have attached the company logo, one in black and one in white. Please provide a design in black background and the other in white background. Please include "Accounting, Tax & Consulting Services". I want the business card to be clean and very professional.

```html
<!DOCTYPE html>
<html lang="en">
<head>
<meta charset="utf-8">
<title>Dario Whitcombe, CPA LLC – Business Cards</title>
<link rel="stylesheet" href="https://fonts.googleapis.com/css2?family=Montserrat:wght@500;600&family=Arimo:wght@400&display=swap">
<style>
  :root {
    --bg-top: #dcdcdc;
    --bg-bottom: #a9a9a9;
    --card-white: #ffffff;
    --card-dark: #3a3a3c;
    --band-dark: #3b3b3d;
    --brand-red: #a3181c;
    --ink: #2b2b2b;
    --ink-soft: #6e6e6e;
    --rule: #9a9a9a;
    --emboss: #4a4a4c;
    --tagline: #f2f2f2;
  }
  * { box-sizing: border-box; margin: 0; padding: 0; }
  html, body { width: 1200px; height: 788px; overflow: hidden; }
  body {
    position: relative;
    background: linear-gradient(180deg, var(--bg-top), var(--bg-bottom));
    font-family: "Arimo", Arial, sans-serif;
  }
  .card {
    position: absolute;
    width: 520px;
    height: 297px;
    border-radius: 22px;
    overflow: hidden;
    box-shadow: 0 14px 30px rgba(0,0,0,.28);
  }

  /* Front card */
  .card-front { left: 70px; top: 130px; background: var(--card-white); }
  .brand-mark {
    position: absolute; right: 38px; top: 46px;
    display: flex; align-items: center; gap: 10px;
  }
  .brand-mark .square { width: 14px; height: 14px; background: var(--ink); }
  .brand-mark .brand-name {
    font-family: "Montserrat", sans-serif; font-weight: 600;
    font-size: 17px; color: var(--ink); letter-spacing: .4px;
  }
  .person { position: absolute; left: 38px; top: 118px; }
  .person-name {
    font-family: "Montserrat", sans-serif; font-weight: 600;
    font-size: 22px; color: var(--brand-red); letter-spacing: .3px;
  }
  .person-title { font-size: 13px; color: var(--ink); margin-top: 2px; }
  .divider {
    position: absolute; left: 38px; right: 38px; top: 176px;
    height: 1px; background: var(--rule);
  }
  .contact-list {
    position: absolute; left: 38px; top: 190px; list-style: none;
  }
  .contact-list li {
    display: flex; align-items: center; gap: 7px;
    font-size: 12.5px; color: var(--ink); line-height: 19px;
  }
  .contact-list svg { width: 11px; height: 11px; flex: none; }
  .address {
    position: absolute; right: 38px; top: 196px; text-align: right;
    font-size: 12.5px; color: var(--ink); line-height: 18px;
  }
  .edge-band { position: absolute; left: 0; bottom: 0; width: 520px; height: 14px; }

  /* Back card */
  .card-back { left: 610px; top: 380px; background: var(--card-dark); }
  .back-mark {
    position: absolute; left: 0; right: 0; top: 96px;
    display: flex; justify-content: center; align-items: center; gap: 14px;
  }
  .back-mark .square { width: 22px; height: 22px; background: var(--emboss); }
  .back-mark .brand-name {
    font-family: "Montserrat", sans-serif; font-weight: 600;
    font-size: 26px; color: var(--emboss); letter-spacing: .6px;
    text-shadow: 0 1px 0 rgba(255,255,255,.06), 0 -1px 0 rgba(0,0,0,.35);
  }
  .tagline {
    position: absolute; left: 0; right: 0; top: 212px; text-align: center;
    font-size: 15px; letter-spacing: 2.2px; color: var(--tagline);
  }
</style>
</head>
<body>

<section class="card card-front" aria-label="Business card front">
  <div class="brand-mark">
    <span class="square"></span>
    <span class="brand-name">Dario Whitcombe, CPA LLC</span>
  </div>

  <div class="person">
    <p class="person-name">DARIO WHITCOMBE</p>
    <p class="person-title">Principal</p>
  </div>

  <div class="divider"></div>

  <ul class="contact-list">
    <li>
      <svg viewBox="0 0 12 12" aria-hidden="true"><circle cx="6" cy="6" r="6" fill="#a3181c"/><path d="M4 3.2l1 1.4-.6.7c.4.9 1.1 1.6 2 2l.7-.6 1.4 1-.5 1C5.6 8.5 3.5 6.4 3.3 4.1z" fill="#fff"/></svg>
      215-630-2918
    </li>
    <li>
      <svg viewBox="0 0 12 12" aria-hidden="true"><circle cx="6" cy="6" r="6" fill="#a3181c"/><rect x="3" y="4" width="6" height="4.2" fill="#fff"/><path d="M3 4l3 2.3L9 4" fill="none" stroke="#a3181c" stroke-width=".7"/></svg>
      info@dariowhitcombecpa.com
    </li>
    <li>
      <svg viewBox="0 0 12 12" aria-hidden="true"><circle cx="6" cy="6" r="6" fill="#a3181c"/><circle cx="6" cy="6" r="3" fill="none" stroke="#fff" stroke-width=".8"/><path d="M3 6h6M6 3c-1.4 1.6-1.4 4.4 0 6M6 3c1.4 1.6 1.4 4.4 0 6" fill="none" stroke="#fff" stroke-width=".6"/></svg>
      www.dariowhitcombecpa.com
    </li>
  </ul>

  <address class="address" style="font-style:normal">
    1480 N Alder Avenue<br>
    Brennick County Name 6042
  </address>

  <svg class="edge-band" viewBox="0 0 520 14" preserveAspectRatio="none" aria-hidden="true">
    <polygon points="0,0 300,0 292,14 0,14" fill="var(--brand-red)"/>
    <polygon points="304,0 520,0 520,14 296,14" fill="var(--band-dark)"/>
  </svg>
</section>

<section class="card card-back" aria-label="Business card back">
  <div class="back-mark">
    <span class="square"></span>
    <span class="brand-name">Dario Whitcombe, CPA LLC</span>
  </div>
  <p class="tagline">Accounting, Tax &amp; Consulting Services</p>
</section>

</body>
</html>
```